Business Card Design for company

We want new business cards. We'd like something different-- yet still highly professional. Our tagline is Building clarity, engineering results. Stock photos are ok, as long as they are relevant and look upscale.

Target Market(s)

Architecture/Business Management Consulting/Engineering Consulting

Contact Information for Business Card

dark gray background with pops of blue might be good, but you tell me. You're the designers. Rounded corners might be nice, but again, you tell me.

Font styles to use
Serif
Sans Serif

Colors
3276b5
5c5c5c
9d9d9d
fbfbfb

Requirements
Nice to have
• Something different, but still very professional.

```html
<!DOCTYPE html>
<html lang="en">
<head>
<meta charset="utf-8">
<title>Corven Partners – Business Card</title>
<link rel="stylesheet" href="https://fonts.googleapis.com/css2?family=Montserrat:wght@500;600&family=Open+Sans:wght@400&display=swap">
<style>
  :root {
    --brand-blue: #3276b5;
    --deep-blue: #2a64a0;
    --charcoal: #474b52;
    --text-gray: #5c5c5c;
    --mid-gray: #9d9d9d;
    --card-light: #e6e6e6;
    --page-bg: #f1f1f1;
    --tagline-white: #fbfbfb;
  }
  * { box-sizing: border-box; margin: 0; padding: 0; }
  html, body { width: 1200px; height: 896px; overflow: hidden; }
  body {
    background: var(--page-bg);
    display: flex;
    flex-direction: column;
    align-items: center;
    justify-content: center;
    gap: 52px;
    font-family: "Open Sans", sans-serif;
  }
  .card {
    position: relative;
    width: 640px;
    height: 366px;
    border-radius: 4px;
    overflow: hidden;
    box-shadow: 0 10px 26px rgba(0,0,0,0.18);
  }

  /* Front */
  .card-front { background: var(--card-light); }
  .front-brand {
    position: absolute;
    left: 48px; top: 112px;
    width: 250px;
    font-family: "Montserrat", sans-serif;
    font-weight: 600;
    color: var(--brand-blue);
    text-transform: uppercase;
    line-height: 1.05;
  }
  .front-brand .brand-line-1 { display: block; font-size: 52px; letter-spacing: 2px; }
  .front-brand .brand-line-2 { display: block; font-size: 24px; letter-spacing: 6px; margin-top: 6px; }
  .divider {
    position: absolute;
    left: 320px; top: 96px;
    width: 1px; height: 170px;
    background: var(--mid-gray);
  }
  .contact {
    position: absolute;
    left: 344px; top: 104px;
    color: var(--text-gray);
  }
  .contact-name {
    font-family: "Montserrat", sans-serif;
    font-weight: 600;
    font-size: 20px;
    letter-spacing: 1px;
    text-transform: uppercase;
    color: var(--brand-blue);
  }
  .contact-name .surname { color: var(--charcoal); }
  .contact-role { font-size: 15px; margin: 2px 0 8px; }
  .contact-list { list-style: none; font-size: 14px; line-height: 1.6; }
  .contact-list li { display: flex; align-items: center; gap: 8px; }
  .contact-list svg { width: 12px; height: 12px; fill: var(--brand-blue); flex: none; }
  .contact-address { font-size: 14px; line-height: 1.45; margin-top: 6px; }
  .front-band {
    position: absolute; left: 0; right: 0; bottom: 0;
    height: 20px;
    display: flex;
  }
  .front-band .band-blue { width: 46%; background: var(--deep-blue); }
  .front-band .band-dark { flex: 1; background: var(--charcoal); }

  /* Back */
  .card-back { background: var(--charcoal); }
  .back-brand {
    position: absolute;
    right: 56px; top: 88px;
    text-align: right;
    font-family: "Montserrat", sans-serif;
    font-weight: 600;
    color: var(--deep-blue);
    text-transform: uppercase;
    line-height: 1.05;
  }
  .back-brand .brand-line-1 { display: block; font-size: 60px; letter-spacing: 2px; }
  .back-brand .brand-line-2 { display: block; font-size: 27px; letter-spacing: 7px; margin-top: 6px; }
  .tagline-band {
    position: absolute;
    left: 0; bottom: 0;
    width: 100%;
    height: 46px;
    background: var(--deep-blue);
    display: flex;
    align-items: center;
    padding-left: 36px;
  }
  .tagline {
    font-family: "Montserrat", sans-serif;
    font-weight: 500;
    font-size: 17px;
    letter-spacing: 1px;
    color: var(--tagline-white);
    text-transform: uppercase;
    white-space: nowrap;
  }
</style>
</head>
<body>

  <section class="card card-front" aria-label="Card front">
    <div class="front-brand">
      <span class="brand-line-1">Corven</span>
      <span class="brand-line-2">Partners</span>
    </div>
    <div class="divider"></div>
    <div class="contact">
      <p class="contact-name">Daniel <span class="surname">Reyes</span></p>
      <p class="contact-role">Managing Director</p>
      <ul class="contact-list">
        <li>
          <svg viewBox="0 0 12 12" aria-hidden="true"><path d="M1 4c0-2 2-3 5-3s5 1 5 3l-2 1-1-2H4L3 5 1 4zM3 6h6l1 5H2z"/></svg>
          044-555 010 200
        </li>
        <li>
          <svg viewBox="0 0 12 12" aria-hidden="true"><path d="M3 0h6a1 1 0 0 1 1 1v10a1 1 0 0 1-1 1H3a1 1 0 0 1-1-1V1a1 1 0 0 1 1-1zm0 2v7h6V2z"/></svg>
          044-555 010 201
        </li>
        <li>
          <svg viewBox="0 0 12 12" aria-hidden="true"><path d="M0 2h12v1L6 7 0 3zM0 4.5l6 4 6-4V10H0z"/></svg>
          hello@corvenpartners.com
        </li>
        <li>
          <svg viewBox="0 0 12 12" aria-hidden="true"><circle cx="6" cy="6" r="6"/></svg>
          www.corvenpartners.com
        </li>
      </ul>
      <p class="contact-address">48 Harbour Lane, Ashford,<br>Westland, 20415.</p>
    </div>
    <div class="front-band"><span class="band-blue"></span><span class="band-dark"></span></div>
  </section>

  <section class="card card-back" aria-label="Card back">
    <div class="back-brand">
      <span class="brand-line-1">Corven</span>
      <span class="brand-line-2">Partners</span>
    </div>
    <div class="tagline-band">
      <p class="tagline">Building clarity, engineering results</p>
    </div>
  </section>

</body>
</html>
```